Probate (Legal) Wordpress Design with Coding for Online Company

I need a Wordpress design with coding, pictures, content to be provided by me, fully responsive, and development. This is for a 6-7 page design.

Pages Needed: Home/About/Probate/Process/FAQ/Contact Us/Blog.

The home page should be organized as followed:
-Steps in Probate: Gather; Implement; Close (each step will come with content)
-Flat-Fee Price & Savings: Content will go here with a button to contact us (phone number) or just the phone number.
-You Have Questions, We Have Answers: five questions with content. Only one question answer to show at a time when clicked on the question from the list.
-Get to Know Us: a brief description with content about what we do and who we are.

Main image slogan: Helping Californians deal with loss with DIGNITY & UNDERSTATING (you may use a better slogan if you wish).

The Contact page should not have a map since we are an online company. We service the entire state of California in every county and city.

The About page should be simple, direct, and easy on the eye. It should have a brief description of who we are and it should have no more than 6 reasons why the client should hire us.

About our online California company. We are not attorneys but legal document assistants who prepare legal documents for probate estate when someone dies with or without a will and assets need to be distributed. We have a flat-fee for Formal Probate of $999 and $699 for Informal Probate. We are an online company and offer our services to the entire state of California in every county. We do everything over the phone and email. The turn around time for us to prepare the initial legal paperwork for the client is within 3-5 business days. We can prepare, file, serve and manage a probate matter from petition to closing. We are not attorneys so our prices are very affordable compare to the attorney.

The company name for the website will be www.velmarhollow.com, The Velmar Hollow Group.

I do not have a logo yet. The colors of the website should be easy on the eye and calming. THE SITE SHOULD BE SIMPLE AND STRAIGHT TO THE POINT. EASY TO NAVIGATE.

The company phone number should be very visible and should stand out to the client. It should also be clickable and ready to dial for smartphone users.

I do not want a contact form on the homepage. THE MAIN THING IS FOR THE POTENTIAL CLIENT TO CALL OUR OFFICE TO SIGN UP.

I do like some images of family or people since we are dealing with people who just lost a loved one. Not all the images have to be of people.

The site should not look like we practice law or that people can mistake us for attorneys.

Target Market(s)

People who just lost a loved one who had property, assets, in California but died with or without a will or trust. This is for people looking to hire non-attorneys.

Coding

Coded - Design and coding required

Font styles to use
Serif

Colors

Designer to choose colors to be used in the design.

Requirements
Must have
• Refer to Project Description.
Nice to have
• The sample images provided is what I am attracted to for the homepage image.
Should not have

```html
<!DOCTYPE html>
<html lang="en">
<head>
<meta charset="utf-8">
<title>The Velmar Hollow Group – Probate Document Assistance</title>
<link href="https://fonts.googleapis.com/css2?family=PT+Serif:wght@400;700&family=Open+Sans:wght@400;600&display=swap" rel="stylesheet">
<style>
:root{
  --blue:#0a67b3;
  --blue-dark:#08558f;
  --olive:#9ba62c;
  --olive-light:#dfe2b8;
  --ink:#222;
  --body:#555;
  --steel:#54565c;
  --mist:#f2f2f2;
  --white:#fff;
  --serif:'PT Serif', Georgia, serif;
  --sans:'Open Sans', Arial, sans-serif;
}
*{box-sizing:border-box;margin:0;padding:0}
html,body{width:1200px;height:3125px;overflow:hidden}
body{font-family:var(--sans);color:var(--body);background:var(--white);position:relative}
section,header,footer{position:relative;width:1200px;overflow:hidden}
.abs{position:absolute}
h2{font-family:var(--serif);font-weight:700;color:var(--ink);font-size:33px}
.btn{position:absolute;display:flex;align-items:center;justify-content:center;background:var(--blue);color:var(--white);font-family:var(--serif);font-weight:700;font-size:15px;text-transform:uppercase;border-bottom:3px solid var(--blue-dark);box-shadow:0 2px 4px rgba(0,0,0,.25);text-decoration:none}

/* header */
.site-header{height:108px;background:var(--white);box-shadow:0 1px 4px rgba(0,0,0,.1);z-index:2}
.brand{left:100px;top:26px;display:flex;align-items:center;gap:12px}
.brand-mark{width:46px;height:46px;border-radius:50%;border:3px solid var(--olive)}
.brand-name{font-family:var(--serif);font-weight:700;font-size:26px;color:#3b6a2a}
.phone-pill{left:788px;top:17px;width:152px;height:30px;background:var(--blue);border-radius:3px;color:var(--white);font-size:12px;display:flex;align-items:center;padding-left:10px;gap:10px}
.phone-pill .ico{width:22px;height:22px;border-radius:50%;background:var(--white);display:flex;align-items:center;justify-content:center}
.social{left:970px;top:16px;display:flex;gap:9px}
.social span{width:26px;height:26px;border-radius:50%;background:var(--olive-light);border:1px solid #c7cb8c}
.main-nav{right:100px;top:72px;display:flex;gap:34px;font-family:var(--serif);font-weight:700;font-size:15px;color:var(--ink)}
.main-nav a{color:inherit;text-decoration:none}
.main-nav a.current{color:var(--blue)}

/* hero */
.hero{height:459px}
.hero-photo{inset:0;background:linear-gradient(90deg,#5b6a3e 0%,#8a8a5c 30%,#9fae7a 55%,#b7c496 75%,#8fa46a 100%)}
.hero-copy{left:528px;top:135px;color:var(--white);font-family:var(--serif);font-weight:700;text-shadow:0 2px 3px rgba(0,0,0,.35)}
.hero-copy .lead{font-size:29px}
.hero-copy .big{font-size:44px;margin-top:6px;letter-spacing:.5px}
.hero .btn{left:530px;top:259px;width:170px;height:46px}
.dots{left:1072px;top:399px;display:flex;gap:4px}
.dots span{width:14px;height:14px;border-radius:50%;border:2px solid var(--white)}
.dots span.on{background:var(--white)}

/* steps */
.steps{height:441px;background:linear-gradient(180deg,#4f5156,#5e6066 60%,#55575c);color:var(--white)}
.steps h2{color:var(--white);text-align:center;padding-top:70px}
.step{width:280px;text-align:center;top:150px}
.step .circle{width:90px;height:90px;border-radius:50%;background:var(--olive);margin:0 auto;display:flex;align-items:center;justify-content:center}
.step h3{font-family:var(--serif);font-weight:400;font-size:22px;margin-top:18px}
.step p{font-size:14px;line-height:24px;margin-top:2px;padding:0 25px}
.chev{top:198px;color:#b9bcc2;font-size:30px;letter-spacing:-6px;font-family:var(--sans)}

/* who */
.who{height:473px}
.who h2{left:104px;top:90px;position:absolute}
.who .copy{left:104px;top:155px;width:430px;font-size:14px;line-height:24px}
.who .copy p+p{margin-top:14px}
.who .btn{left:104px;top:322px;width:170px;height:48px}
.who-photo{left:583px;top:72px;width:514px;height:323px;border:5px solid var(--white);box-shadow:0 0 4px rgba(0,0,0,.3);background:linear-gradient(120deg,#d9dce3,#b7bdc9 50%,#4a5670 85%)}

/* flat fee */
.fee{height:479px}
.fee-photo{inset:0;background:linear-gradient(90deg,#24324f 0%,#6c7c93 30%,#9fb4c4 55%,#7f98ab 100%)}
.fee h2{color:var(--white);left:675px;top:100px;position:absolute}
.fee p{left:677px;top:160px;width:430px;color:var(--white);font-size:15px;line-height:24px}
.fee .btn{left:677px;top:325px;width:170px;height:48px}

/* what we do */
.what{height:380px}
.what h2{text-align:center;padding-top:68px}
.what .intro{width:540px;margin:18px auto 0;text-align:center;font-size:14px;line-height:24px}
.service{top:215px;width:200px;text-align:center}
.service svg{display:block;margin:0 auto}
.service h3{font-family:var(--serif);font-weight:400;font-size:19px;color:var(--blue);margin-top:12px}

/* faq */
.faq{height:450px;background:var(--mist)}
.faq h2{text-align:center;padding-top:70px}
.faq-list{left:103px;top:157px;width:500px;list-style:none}
.faq-list li{height:36px;border:1px solid #c9c9c9;background:var(--white);margin-bottom:7px;font-family:var(--serif);font-size:16px;color:var(--ink);padding-left:36px;line-height:34px}
.faq-list li.open{background:var(--blue);color:var(--white);border-color:var(--blue);position:relative}
.faq-list li.open::after{content:"";position:absolute;right:-30px;top:-1px;border-left:30px solid var(--blue);border-top:18px solid transparent;border-bottom:18px solid transparent}
.faq-answer{left:653px;top:153px;width:447px;height:222px;background:#eef0dc;border:1px solid #c9cd98;padding:30px 28px;font-size:14px;line-height:24px}

/* footer */
.site-footer{height:335px;background:linear-gradient(180deg,#8c9aa8,#9fadb9 60%,#7f8d99);color:var(--white)}
.site-footer h4{font-family:var(--serif);font-weight:700;font-size:18px}
.f-about{left:128px;top:58px;width:260px;font-size:13px;line-height:21px}
.f-about p{margin-top:18px}
.f-social{display:flex;gap:9px;margin-top:22px}
.f-social span{width:24px;height:24px;border-radius:50%;background:#596573}
.f-links{left:542px;top:58px}
.f-links ul{list-style:none;margin-top:18px;font-size:13px;line-height:20px}
.f-news{left:767px;top:58px;width:300px;font-size:13px;line-height:21px}
.f-news p{margin-top:18px}
.f-form{display:flex;margin-top:12px}
.f-form span{width:220px;height:29px;background:var(--white);color:#888;font-size:12px;padding-left:12px;line-height:29px}
.f-form b{width:70px;height:29px;background:var(--blue);font-family:var(--serif);font-size:14px;text-align:center;line-height:29px}
.f-rule{left:100px;right:100px;top:265px;border-top:1px solid rgba(255,255,255,.4)}
.f-copy{left:0;right:0;top:282px;text-align:center;font-size:12px}
</style>
</head>
<body>

<header class="site-header">
  <div class="abs brand"><span class="brand-mark"></span><span class="brand-name">The Velmar Hollow Group</span></div>
  <div class="abs phone-pill"><span class="ico"><svg width="12" height="12" viewBox="0 0 24 24"><path fill="#0a67b3" d="M6.6 10.8a15 15 0 0 0 6.6 6.6l2.2-2.2c.3-.3.7-.4 1-.2 1.1.4 2.3.6 3.6.6.6 0 1 .4 1 1V20c0 .6-.4 1-1 1A17 17 0 0 1 3 4c0-.6.4-1 1-1h3.5c.6 0 1 .4 1 1 0 1.3.2 2.5.6 3.6.1.3 0 .7-.2 1z"/></svg></span>+1 555 014 2290</div>
  <div class="abs social"><span></span><span></span><span></span><span></span></div>
  <nav class="abs main-nav"><a class="current">Home</a><a>About</a><a>Probate</a><a>Process</a><a>FAQ</a><a>Contact Us</a><a>Blog</a></nav>
</header>

<section class="hero">
  <div class="abs hero-photo" role="img" aria-label="Family with two young children sitting together on the grass in a park"></div>
  <div class="abs hero-copy">
    <div class="lead">Helping Californians deal with loss with</div>
    <div class="big">DIGNITY &amp; UNDERSTATING</div>
  </div>
  <a class="btn">Learn More</a>
  <div class="abs dots"><span class="on"></span><span></span><span></span></div>
</section>

<section class="steps" role="img" aria-label="Steps in probate over a faded city skyline">
  <h2>Steps In Probate</h2>
  <div class="abs step" style="left:75px">
    <div class="circle"><svg width="44" height="44" viewBox="0 0 44 44" fill="none" stroke="#fff" stroke-width="3" stroke-linecap="round"><path d="M4 4l13 13M17 9v8H9M40 4L27 17M27 9v8h8M4 40l13-13M17 35v-8H9M40 40L27 27M27 35v-8h8"/></svg></div>
    <h3>Gather</h3>
    <p>Lorem ipsum dolor sit amet, conectr adipiscing elit, sed do eiusmod tempor incididunt ut labore magna aliqua.</p>
  </div>
  <div class="abs chev" style="left:398px">»&nbsp;»</div>
  <div class="abs step" style="left:460px">
    <div class="circle"><svg width="44" height="44" viewBox="0 0 44 44" fill="none" stroke="#fff" stroke-width="3" stroke-linejoin="round"><path d="M30 6l8 8-20 20-10 2 2-10z M26 10l8 8 M8 36l-2 2"/></svg></div>
    <h3>Implement</h3>
    <p>Lorem ipsum dolor sit amet, conectr adipiscing elit, sed do eiusmod tempor incididunt ut labore magna aliqua.</p>
  </div>
  <div class="abs chev" style="left:785px">»&nbsp;»</div>
  <div class="abs step" style="left:845px">
    <div class="circle"><svg width="44" height="44" viewBox="0 0 44 44" fill="none" stroke="#fff" stroke-width="4" stroke-linecap="round"><path d="M22 4v16 M13 10a15 15 0 1 0 18 0"/></svg></div>
    <h3>Close</h3>
    <p>Lorem ipsum dolor sit amet, conectr adipiscing elit, sed do eiusmod tempor incididunt ut labore magna aliqua.</p>
  </div>
</section>

<section class="who">
  <h2>Who We Are ?</h2>
  <div class="abs copy">
    <p>Lorem ipsum dolor sit amet, consectetur adipiscing elit, sed do eiusmod tempor incididunt ut labore et dolore magna aliqua.</p>
    <p>Duis aute irure dolor in reprehenderit in voluptate velit esse cillum dolore eu fugiat nulla pariatur. Excepteur sint occaecat cupidatat non proident, sunt in culpa qui officia deserunt mollit anim id est laborum.</p>
  </div>
  <a class="btn">Learn More</a>
  <div class="abs who-photo" role="img" aria-label="Elderly couple reviewing documents at a table with a young woman and a document assistant"></div>
</section>

<section class="fee">
  <div class="abs fee-photo" role="img" aria-label="Two colleagues in an office reviewing information on a tablet"></div>
  <h2>Flat-Fee Price &amp; Savings</h2>
  <p class="abs">Lorem ipsum dolor sit amet, consectetur adipiscing elit, sed do eiusmod tempor incididunt ut labore et dolore magna aliqua. Ut enim ad minim veniam, quis nostrud exercitation ullamco laboris nisi ut aliquip ex ea commodo consequat. Duis aute irure dolor in reprehenderit in voluptate velit esse cillum dolore eu fugiat nulla pariatur.</p>
  <a class="btn">Contact Us</a>
</section>

<section class="what">
  <h2>What We Do ?</h2>
  <p class="intro">Lorem ipsum dolor sit amet, consectetur adipiscing elit, sed do eiusmod tempor incididunt ut labore et dolore magna aliqua.</p>
  <div class="abs service" style="left:128px">
    <svg width="50" height="46" viewBox="0 0 50 46"><rect x="18" y="2" width="14" height="8" fill="none" stroke="#9ba62c" stroke-width="3"/><rect x="2" y="10" width="46" height="34" fill="#9ba62c"/><rect x="2" y="22" width="46" height="3" fill="#fff"/></svg>
    <h3>Estate Planning</h3>
  </div>
  <div class="abs service" style="left:385px">
    <svg width="50" height="46" viewBox="0 0 50 46" fill="#9ba62c"><path d="M25 4c-5 4-5 10 0 14c5-4 5-10 0-14z"/><path d="M2 22l6 0 10 12h14l4-4 6 0 0-8 6 0-10 22H14z"/><rect x="24" y="18" width="2" height="8"/></svg>
    <h3>Diligence</h3>
  </div>
  <div class="abs service" style="left:642px">
    <svg width="46" height="46" viewBox="0 0 46 46" fill="#9ba62c"><circle cx="23" cy="12" r="10"/><path d="M2 46c0-14 9-21 21-21s21 7 21 21z"/></svg>
    <h3>Assistance</h3>
  </div>
  <div class="abs service" style="left:898px">
    <svg width="40" height="48" viewBox="0 0 40 48"><rect x="2" y="2" width="36" height="44" fill="#9ba62c"/><rect x="10" y="12" width="20" height="3" fill="#fff"/><rect x="10" y="19" width="20" height="3" fill="#fff"/></svg>
    <h3>Guidance</h3>
  </div>
</section>

<section class="faq">
  <h2>Frequently Asked Questions</h2>
  <ul class="abs faq-list">
    <li class="open">Lorem ipsum dolor sit amet consectetur adipiscing elit ?</li>
    <li>Lorem ipsum dolor sit amet consectetur adipiscing elit ?</li>
    <li>Lorem ipsum dolor sit amet consectetur adipiscing elit ?</li>
    <li>Lorem ipsum dolor sit amet consectetur adipiscing elit ?</li>
    <li>Lorem ipsum dolor sit amet consectetur adipiscing elit ?</li>
  </ul>
  <div class="abs faq-answer">Lorem ipsum dolor sit amet, consectetur adipiscing elit, sed do eiusmod tempor incididunt ut labore et dolore magna aliqua. Ut enim ad minim veniam, quis nostrud exercitation ullamco laboris nisi ut aliquip ex ea commodo consequat. Duis aute irure dolor in reprehenderit in voluptate velit esse cillum dolore eu fugiat nulla pariatur.</div>
</section>

<footer class="site-footer" role="img" aria-label="Footer over a faded bay bridge and city skyline">
  <div class="abs f-about">
    <h4>About Us</h4>
    <p>Lorem ipsum dolor sit amet, consectetur adipiscing elit, sed do eiusmod tempor incidi dunt ut labore et dolore magna aliqua.</p>
    <div class="f-social"><span></span><span></span><span></span><span></span></div>
  </div>
  <div class="abs f-links">
    <h4>Links</h4>
    <ul><li>Home</li><li>About</li><li>Probate</li><li>Process</li><li>FAQ</li><li>Contact Us</li><li>Blog</li></ul>
  </div>
  <div class="abs f-news">
    <h4>Newsletter Subscription</h4>
    <p>Lorem ipsum dolor sit amet, consectetur adipiscing elit, sed do eiusmod tempor.</p>
    <div class="f-form"><span>Enter Your Email</span><b>Submit</b></div>
  </div>
  <div class="abs f-rule"></div>
  <div class="abs f-copy">Copyright © 2017 The Velmar Hollow Group - All Rights Reserved.</div>
</footer>

</body>
</html>
```